KTR Design Business Card

I need to develop a business card for my real estate design and investment company. Something clean, classic and professional with a modern vibe.

Industry/Entity Type

Real Estate

Font styles to use
Serif
Sans Serif

```html
<!DOCTYPE html>
<html lang="en">
<head>
<meta charset="UTF-8">
<title>KTR Design Business Card</title>
<link href="https://fonts.googleapis.com/css2?family=Questrial&family=Open+Sans:wght@600;700&family=Libre+Baskerville:wght@700&display=swap" rel="stylesheet">
<style>
  :root {
    --backdrop: #262626;
    --card-dark: #3a3a3a;
    --card-light: #ffffff;
    --light-fade: #e9e9e9;
    --ink: #1c1c1c;
    --stripe: #8a8a8a;
    --name-grey: #6e6e6e;
    --logo-soft: #d6d6d6;
    --tagline: #9a9a9a;
    --contact-text: #f2f2f2;
  }
  html, body {
    margin: 0;
    width: 1200px;
    height: 997px;
    overflow: hidden;
    background: var(--backdrop);
  }
  .stage {
    width: 1200px;
    height: 997px;
    display: flex;
    flex-direction: column;
    align-items: center;
    justify-content: center;
    gap: 56px;
  }
  .card {
    width: 700px;
    height: 400px;
    border-radius: 22px;
    position: relative;
    overflow: hidden;
    box-shadow: 0 14px 34px rgba(0,0,0,0.45);
  }
  /* back side */
  .card-back {
    background: var(--card-dark);
    display: flex;
    flex-direction: column;
    align-items: center;
    justify-content: center;
  }
  .card-back .brand-name {
    font-family: "Questrial", sans-serif;
    font-size: 64px;
    color: var(--logo-soft);
    letter-spacing: 1px;
  }
  .card-back .tagline {
    margin-top: 26px;
    font-family: "Questrial", sans-serif;
    font-size: 15px;
    letter-spacing: 6px;
    color: var(--tagline);
  }
  /* front side */
  .card-front {
    background: var(--card-dark);
  }
  .front-top {
    position: absolute;
    left: 0; top: 0;
    width: 100%;
    height: 228px;
    background: linear-gradient(180deg, var(--card-light) 0%, var(--light-fade) 100%);
  }
  .front-top .brand-name {
    position: absolute;
    left: 0; right: 0;
    top: 62px;
    text-align: center;
    font-family: "Questrial", sans-serif;
    font-size: 60px;
    color: var(--ink);
  }
  .person {
    position: absolute;
    right: 36px;
    bottom: 22px;
    text-align: center;
  }
  .person-name {
    font-family: "Libre Baskerville", serif;
    font-weight: 700;
    font-size: 20px;
    color: var(--name-grey);
    letter-spacing: 1px;
  }
  .person-role {
    font-family: "Open Sans", sans-serif;
    font-weight: 700;
    font-size: 11px;
    color: var(--name-grey);
    letter-spacing: 0.5px;
  }
  .stripes {
    position: absolute;
    left: 0;
    top: 228px;
    width: 100%;
    height: 18px;
    background: var(--card-light);
  }
  .stripes span {
    position: absolute;
    left: 0; width: 100%;
    height: 2px;
    background: var(--stripe);
  }
  .stripes span:nth-child(1) { top: 3px; }
  .stripes span:nth-child(2) { top: 8px; }
  .stripes span:nth-child(3) { top: 13px; }
  .contacts {
    position: absolute;
    left: 44px;
    top: 272px;
    list-style: none;
    margin: 0; padding: 0;
    display: flex;
    flex-direction: column;
    gap: 14px;
  }
  .contacts li {
    display: flex;
    align-items: center;
    gap: 16px;
    font-family: "Open Sans", sans-serif;
    font-weight: 600;
    font-size: 15px;
    color: var(--contact-text);
  }
  .contacts svg {
    width: 20px;
    height: 20px;
    flex: none;
  }
</style>
</head>
<body>
<main class="stage">
  <section class="card card-back" aria-label="Card back">
    <div class="brand-name">KTR Design</div>
    <div class="tagline">WE KNOW INVESTMENTS BETTER</div>
  </section>

  <section class="card card-front" aria-label="Card front">
    <div class="front-top">
      <div class="brand-name">KTR Design</div>
      <div class="person">
        <div class="person-name">DAN HARLOW</div>
        <div class="person-role">PROJECT LEADER</div>
      </div>
    </div>
    <div class="stripes"><span></span><span></span><span></span></div>
    <ul class="contacts">
      <li>
        <svg viewBox="0 0 20 20" aria-hidden="true"><rect x="5" y="1.5" width="10" height="17" rx="1.5" fill="none" stroke="#f2f2f2" stroke-width="1.8"/></svg>
        0400 123 987
      </li>
      <li>
        <svg viewBox="0 0 20 20" aria-hidden="true"><rect x="2" y="4.5" width="16" height="11" fill="#f2f2f2"/><path d="M2 4.5 L10 11 L18 4.5" fill="none" stroke="#3a3a3a" stroke-width="1.5"/></svg>
        danharlow@ktrdesign.com
      </li>
      <li>
        <svg viewBox="0 0 20 20" aria-hidden="true"><g fill="none" stroke="#f2f2f2" stroke-width="1.8" stroke-linecap="round"><path d="M8.5 11.5 L11.5 8.5"/><path d="M9 6 L11 4 a3 3 0 0 1 5 5 L14 11"/><path d="M11 14 L9 16 a3 3 0 0 1 -5 -5 L6 9"/></g></svg>
        www.ktrdesign.com
      </li>
    </ul>
  </section>
</main>
</body>
</html>
```